Agrarhandel benötigt Homepage
Zielgruppe
Wir sind ein Agrarhandel mit einem Warenumschlagslager im Sinne eines klassischen Einzelhandels und vertreiben Produkte an Landwirte.
Wir vertreiben folgende Hauptproduktgruppen:
Einzelfuttermittel
wie z.B. Sojaexktraktionsschrot. Die einzelnen Produkte könnten z.B. wie die Futtermittel auf folgender Seite dargestellt werden (https://www.kornprobe-beispiel.eu/de/produkt/trelomixan)
Mischfuttermittel
Hier bieten wir unseren Kunden an, individuelles Mischfutter auf Basis unserer Einzelfuttermittel herzustellen.
Weitere Details und weitere Produktbereiche habe ich in einer Powerpoint-Übersicht dargestellt.
Neben diesen Produkten wollen wir uns als Familienunternehmen selbst vorstellen. Zudem betreiben wir in unserer Familie zusätzlich einen Milchviehbetrieb den wir ebenfalls hervorheben möchten, da wir unseren Kunden gegenüber einerseits als Zulieferer aber auch als Kollege auftreten wollen.
Einzelfuttermittel: Hier können wir durch unsere Unabhängigkeit punkten, da wir nicht abhängig von bestimmten Lieferanten sind und dementsprechend unabhängig beraten können. Wir untersuchen im Vergleich zu unseren Wettbewerben die Qualität der Futtermittel bis ins Detail und können daher eine Transparenz bieten, die Konkurrenten in der Regel nicht bieten können. Unser Warenumschlagsplatz mit moderner Technik ermöglicht es uns äußerst kosteneffizient die Waren umschlagen und ausliefern zu können.
Mischfuttermittel: Auf Basis der vorhandenen Einzelfuttermittel stellen wir je nach Kundenwunsch individuelle Mischfutter her. Wir arbeiten mit offenen Deklarationen, sodass unsere Kunden jederzeit nachvollziehen können, ob auch die Einzelfuttermittel verwendet wurden, die sie bestellt haben und keine billigen Ersatzprodukte verwendet wurden.
Zudem sind wir BT und HUPA zertifiziert. Die aktuellen für unser Unternehmen ausgestellten Zertifikate müssen für unsere Kunden als Download zur Verfügung stehen. Statt dem HUPA-Logo bitte das ..
Aufgabenstellung
Wir möchten gerne ein zeitgemäße Homepage, jedoch muss auch berücksichtigt werden, dass unsere Kunden eher konservativ denken.

```html
<!DOCTYPE html>
<html lang="de">
<head>
<meta charset="utf-8">
<title>Talgrund Agrarhandel – Ihr zuverlässiger Partner im Agrarhandel</title>
<link href="https://fonts.googleapis.com/css2?family=DM+Sans:wght@400;500;700&family=Caveat:wght@400&display=swap" rel="stylesheet">
<style>
:root{
  --green:#1c6a4e;
  --green-light:#2d8a63;
  --orange:#f6a51f;
  --bg:#f2f1ed;
  --ink:#2e2e2e;
  --white:#ffffff;
  --sans:'DM Sans',Arial,sans-serif;
  --script:'Caveat',cursive;
}
*{box-sizing:border-box;margin:0;padding:0}
html,body{width:1200px;height:4647px;overflow:hidden}
body{background:var(--bg);font-family:var(--sans);color:var(--ink);position:relative}
.abs{position:absolute}
.script{font-family:var(--script);color:var(--green);font-size:24px;margin-left:8px}
.section-title{font-weight:400;color:var(--green);font-size:34px;line-height:1}
.section-title .line1{display:block}
.btn{display:inline-block;background:var(--orange);color:var(--white);font-size:13px;letter-spacing:3px;text-transform:uppercase;padding:9px 26px;font-weight:500}

/* Hero */
.hero{left:0;top:0;width:1200px;height:750px}
.hero-photo{position:absolute;inset:0;background:linear-gradient(180deg,#efece5 0%,#e8e2d6 45%,#b79f7f 70%,#6b5337 88%,#3d2e20 100%)}
.nav-logo{left:78px;top:24px;display:flex;align-items:center;gap:8px;color:var(--green);font-weight:700;font-size:15px}
.nav-logo .dot{width:22px;height:22px;border-radius:50%;background:var(--green)}
.nav{right:82px;top:27px;display:flex;gap:26px;align-items:center;font-size:11px;color:var(--ink);text-transform:uppercase}
.nav .btn{font-size:10px;letter-spacing:1px;padding:7px 18px}
.hero-name{left:75px;top:318px;font-size:50px;font-weight:700;color:var(--green);letter-spacing:1px;line-height:1}
.hero-tag{left:78px;top:370px;font-family:var(--script);font-size:36px;color:var(--green);line-height:1}
.cert{left:760px;top:182px;width:370px}
.cert h3{font-size:20px;color:var(--green);font-weight:500;margin-left:52px}
.cert p{font-size:12px;line-height:1.4;margin-left:52px;margin-top:6px;color:var(--ink)}
.cert svg{position:absolute;left:0;top:0}
.hero-rule{left:760px;top:313px;width:360px;height:2px;background:var(--green)}
.side-contact{right:0;top:575px;width:56px}
.side-contact div{height:58px;background:rgba(40,30,20,.75);border-bottom:1px solid rgba(255,255,255,.25);display:flex;align-items:center;justify-content:center}
.scroll-hint{left:586px;top:708px}

/* Highlights */
.hl-title{left:75px;top:826px}
.card{background:var(--white);box-shadow:0 4px 16px rgba(0,0,0,.08)}
.card .img{height:152px}
.card .tag{position:absolute;right:14px;top:128px;width:26px;height:26px;background:#3a2a20}
.card h4{font-weight:400;font-size:24px;color:var(--green);margin:40px 0 0 30px}
.card p{font-size:12px;line-height:1.35;margin:12px 30px 0 30px;color:var(--ink)}
.card .arrow{position:absolute;right:28px;bottom:24px}
.featured{left:598px;top:911px;width:320px;height:435px}
.featured .img{height:178px}
.featured h4{margin:22px 0 0 24px}
.bars{margin:8px 48px 0 24px;font-size:10px}
.bar{margin-bottom:10px}
.bar .track{height:5px;background:#e6e6e6;margin-top:4px;position:relative}
.bar .fill{position:absolute;left:0;top:0;height:5px;background:var(--orange)}
.featured .btn{background:var(--green);position:absolute;left:54px;bottom:30px;font-size:12px;padding:8px 38px}

/* About */
.about-a{left:76px;top:1529px;width:338px;height:424px;background:linear-gradient(160deg,#9a8a6a,#4a3f30 60%,#c59a52)}
.about-b{left:295px;top:1458px;width:263px;height:396px;background:linear-gradient(200deg,#d9d3c6,#8a5a35 50%,#5a3420)}
.about-text{left:690px;top:1540px;width:415px}
.about-text p{font-size:12.5px;line-height:1.38;margin:36px 0 30px}

/* Sortiment */
.sort-title{left:75px;top:2082px}
.tile{overflow:hidden}
.tile .label{position:absolute;left:0;right:0;bottom:0;height:60px;background:rgba(30,60,45,.45);color:var(--white);font-size:24px;text-align:center;line-height:60px}
.tile.small .label{height:auto;background:none;bottom:16px;line-height:1;font-size:24px;text-align:right;padding-right:20px}
.sort-arrow{top:2658px}

/* Generator */
.gen{left:0;top:2886px;width:1200px;height:791px;background:radial-gradient(ellipse at 25% 55%,#8a7664 0%,#3c2e26 45%,#1c1612 100%)}
.gen-text{left:732px;top:3040px;width:390px;color:var(--white)}
.gen-text .section-title,.gen-text .script{color:var(--green-light)}
.gen-text p{font-size:12.5px;line-height:1.4;margin:64px 0 30px}

/* Partners */
.partner-title{left:75px;top:3762px}
.partners{left:0;top:3880px;width:1200px;display:flex;align-items:center;justify-content:space-around;padding:0 40px 0 90px}
.partners span{font-size:30px;font-weight:700;color:#8f8f8f}

/* Footer */
.footer{left:0;top:4116px;width:1200px;height:531px;background:var(--bg);border-top:1px solid #e2e0da}
.f-logo{left:78px;top:4170px;font-size:20px;font-weight:700;color:var(--green);display:flex;gap:10px;align-items:center}
.f-logo .dot{width:34px;height:34px;border-radius:50%;background:var(--orange)}
.news{left:77px;top:4280px;width:365px}
.news input{display:block;width:365px;height:40px;border:none;background:var(--white);font-family:var(--sans);font-size:12px;padding:0 14px;margin-top:20px;color:#888}
.news .check{font-size:9px;margin-top:14px;display:flex;gap:6px;align-items:center}
.news .check i{width:11px;height:11px;border:1px solid #777;display:inline-block}
.news .check a{color:var(--orange);text-decoration:none}
.news .btn{margin-top:16px;padding:10px 26px;font-size:13px}
.fcol{top:4284px;font-size:12px;line-height:1}
.fcol h5{font-size:19px;font-weight:400;color:var(--ink);margin-bottom:14px}
.fcol li{list-style:none;margin-bottom:14px}
.badge{width:136px;height:72px;background:var(--white);border:1px solid #ddd;display:flex;align-items:center;gap:10px;padding:8px}
.badge .mark{width:54px;height:54px;background:#cfd3d0}
.badge .mark2{width:56px;height:50px;background:#e6e6e6}
.social{display:flex;gap:34px;margin-top:10px}
.social i{width:26px;height:26px;border-radius:50%;background:var(--green);display:block}
.bottom-bar{left:0;top:4617px;width:1200px;height:30px;background:var(--green);color:var(--white);font-size:10px;text-align:center;line-height:30px}
</style>
</head>
<body>

<section class="abs hero">
  <div class="hero-photo" role="img" aria-label="Rinder auf einer Weide im Abendlicht"></div>
  <div class="abs nav-logo"><span class="dot"></span>Talgrund</div>
  <nav class="abs nav">
    <span>Über uns</span><span>Produkte ⌄</span><span>Partner</span><span>Downloads</span><span>Kontakt</span><span class="btn">Preisliste</span>
  </nav>
  <div class="abs cert">
    <svg width="42" height="58" viewBox="0 0 42 58"><circle cx="21" cy="21" r="18" fill="none" stroke="#1c6a4e" stroke-width="5"/><circle cx="21" cy="21" r="9" fill="#1c6a4e"/><path d="M10 36 L6 56 L15 50 L21 56 L21 40 Z M32 36 L36 56 L27 50 L21 56 L21 40 Z" fill="#1c6a4e"/></svg>
    <h3>Geprüft und Zertifiziert</h3>
    <p>Wir sind stolz, BT- und HUPA-zertifiziert zu sein – Ihr Vertrauen in unsere Produkte ist dennoch unsere höchste Auszeichnung.</p>
  </div>
  <div class="abs hero-rule"></div>
  <h1 class="abs hero-name">TALGRUND AGRARHANDEL</h1>
  <div class="abs hero-tag">Ihr zuverlässiger Partner im Agrarhandel!</div>
  <div class="abs side-contact">
    <div><svg width="26" height="18" viewBox="0 0 26 18"><rect x="1" y="1" width="24" height="16" fill="none" stroke="#fff" stroke-width="2"/><path d="M1 1 L13 10 L25 1" fill="none" stroke="#fff" stroke-width="2"/></svg></div>
    <div><svg width="14" height="24" viewBox="0 0 14 24"><rect x="1" y="1" width="12" height="22" rx="2" fill="none" stroke="#fff" stroke-width="2"/><circle cx="7" cy="19" r="1.5" fill="#fff"/></svg></div>
    <div><svg width="24" height="24" viewBox="0 0 24 24"><path d="M6 3 l4 0 1 5 -2 2 q2 4 5 5 l2-2 5 1 0 4 q-1 2-3 2 q-15-2-16-16 q0-1 4-1z" fill="none" stroke="#fff" stroke-width="2"/></svg></div>
  </div>
  <svg class="abs scroll-hint" width="28" height="40" viewBox="0 0 28 40"><rect x="2" y="2" width="24" height="36" rx="12" fill="none" stroke="#fff" stroke-width="2"/><path d="M14 10 v14 M9 19 l5 5 5-5" stroke="#fff" stroke-width="2" fill="none"/></svg>
</section>

<h2 class="abs section-title hl-title"><span class="line1">Unser<span class="script">Beste &amp; beliebteste</span></span>Highlight-Sortiment</h2>

<article class="abs card" style="left:-30px;top:938px;width:294px;height:382px">
  <div class="img" role="img" aria-label="Haufen Mischfutter" style="background:radial-gradient(ellipse at 50% 60%,#6f6a4a,#fff 70%)"></div>
  <span class="tag"></span>
  <h4>Rationa Mix 26 / 3PR</h4>
  <p>Eiweißreiches Ergänzungsfutter für Milchrationen mit Sojaschrot, einem Viertel Körnermais, einem Viertel Melasseschnitzel und Rapsschrot</p>
  <svg class="arrow" width="42" height="14" viewBox="0 0 42 14"><path d="M0 7 H40 M34 1 L40 7 L34 13" stroke="#f6a51f" stroke-width="1.6" fill="none"/></svg>
</article>

<article class="abs card" style="left:284px;top:938px;width:300px;height:382px">
  <div class="img" role="img" aria-label="IBC-Container mit Pflanzenrohglyzerin" style="background:radial-gradient(ellipse at 50% 50%,#c9cccd,#fff 65%)"></div>
  <span class="tag"></span>
  <h4>Pflanzenrohglyzerin</h4>
  <p>80% Pflanzenrohglyzerin. Für zuckerreiche und ausgeglichene Rationen</p>
  <svg class="arrow" width="42" height="14" viewBox="0 0 42 14"><path d="M0 7 H40 M34 1 L40 7 L34 13" stroke="#f6a51f" stroke-width="1.6" fill="none"/></svg>
</article>

<article class="abs card featured">
  <div class="img" role="img" aria-label="Haufen Sojaschrot" style="background:radial-gradient(ellipse at 50% 70%,#c9ad8c,#e8ddcf 55%,#fff 80%)"></div>
  <h4>ProteaSoy</h4>
  <div class="bars">
    <div class="bar">Rohprotein 45,2%<div class="track"><span class="fill" style="width:45%"></span></div></div>
    <div class="bar">Rohfaser 12,2%<div class="track"><span class="fill" style="width:12%"></span></div></div>
    <div class="bar">Rohfett 3,3%<div class="track"><span class="fill" style="width:3.5%"></span></div></div>
    <div class="bar">Zucker &amp; Stärke 15,5%<div class="track"><span class="fill" style="width:16%"></span></div></div>
  </div>
  <span class="btn">Zum Produkt</span>
</article>

<article class="abs card" style="left:932px;top:938px;width:300px;height:382px">
  <div class="img" role="img" aria-label="Haufen Rapsschrot" style="background:radial-gradient(ellipse at 50% 65%,#e3b541,#fff 62%)"></div>
  <span class="tag" style="right:44px"></span>
  <h4>ProteaRap</h4>
  <p style="margin-right:40px">Das Futterprotein wird effizient genutzt. Gute Futteraufnahme durch gute Schmackhaftigkeit</p>
  <svg class="arrow" width="42" height="14" viewBox="0 0 42 14" style="right:6px"><path d="M0 7 H40 M34 1 L40 7 L34 13" stroke="#f6a51f" stroke-width="1.6" fill="none"/></svg>
</article>

<div class="abs about-a" role="img" aria-label="Landwirt im Abendlicht auf dem Feld"></div>
<div class="abs about-b" role="img" aria-label="Nahaufnahme eines braun-weißen Rindes"></div>
<div class="abs about-text">
  <h2 class="section-title"><span class="line1">Talgrund<span class="script">Tradition &amp; Moderne</span></span>Agrarhandel</h2>
  <p>Bei Talgrund Agrarhandel GbR sind wir mehr als nur ein Unternehmen – wir sind eine landwirtschaftliche Familie mit tiefen Wurzeln und einem klaren Blick in die Zukunft. Seit 2001 setzen wir auf Tradition, Qualität und persönliche Beziehungen zu unseren Kunden. Unser Engagement erstreckt sich nicht nur auf den Agrarhandel, sondern auch auf einen eigenen Milchviehbetrieb, den wir mit Hingabe führen. Auf unserer "Über uns" Seite möchten wir Ihnen einen Einblick in unsere Geschichte, Werte und die Menschen hinter Talgrund Agrarhandel GbR geben. Tauchen Sie ein in unsere Welt, in der die Verbindung von Tradition und Innovation den Grundstein für unseren Erfolg bildet.</p>
  <span class="btn">Mehr erfahren</span>
</div>

<h2 class="abs section-title sort-title"><span class="line1">Unser<span class="script">Vielseitig &amp; Anspruchsvoll</span></span>Sortiment</h2>

<div class="abs tile" style="left:78px;top:2167px;width:329px;height:379px;background:linear-gradient(150deg,#c9b9a6,#9a5a32 55%,#5b4a3a)" role="img" aria-label="Kalb beim Trinken von Flüssigfutter"><span class="label">Flüssigfutter</span></div>
<div class="abs tile" style="left:434px;top:2167px;width:332px;height:379px;background:linear-gradient(170deg,#8e958f,#6a5040 55%,#4a3a30)" role="img" aria-label="Rind frisst Einzelfutter am Gatter"><span class="label">Einzelfutter</span></div>
<div class="abs tile" style="left:793px;top:2167px;width:326px;height:379px;background:linear-gradient(160deg,#6f7048,#9a6a3e 50%,#5d6a3a)" role="img" aria-label="Rind auf der Weide"><span class="label">Mischfutter</span></div>

<div class="abs tile small" style="left:78px;top:2573px;width:240px;height:192px;background:linear-gradient(150deg,#4a3a2e,#a5835e 60%,#3a2c22)" role="img" aria-label="Hände halten Saatgut"><span class="label">Saatgut</span></div>
<div class="abs tile small" style="left:345px;top:2573px;width:240px;height:192px;background:linear-gradient(180deg,#a9b3b4,#7a8e7e 55%,#6b7e4f)" role="img" aria-label="Siloballen auf einer Wiese"><span class="label">Silofolie</span></div>
<div class="abs tile small" style="left:613px;top:2573px;width:240px;height:192px;background:linear-gradient(160deg,#8a8b6e,#c8c6bd 50%,#6d6a55)" role="img" aria-label="Mineraldünger-Körner auf dem Boden"><span class="label">Mineraldünger</span></div>
<div class="abs tile small" style="left:878px;top:2573px;width:241px;height:192px;background:linear-gradient(160deg,#5a6470,#8a5a3c 55%,#4a3c34)" role="img" aria-label="Rind liegt auf Stallmatten"><span class="label">Stallmatten</span></div>

<svg class="abs sort-arrow" style="left:18px" width="42" height="24" viewBox="0 0 42 24"><path d="M42 12 H2 M12 2 L2 12 L12 22" stroke="#333" stroke-width="2" fill="none"/></svg>
<svg class="abs sort-arrow" style="left:1140px" width="42" height="24" viewBox="0 0 42 24"><path d="M0 12 H40 M30 2 L40 12 L30 22" stroke="#333" stroke-width="2" fill="none"/></svg>

<div class="abs gen" role="img" aria-label="Rind mit weißem Kopf in dunkler Umgebung"></div>
<div class="abs gen-text">
  <h2 class="section-title"><span class="line1">Unser<span class="script">flexibel &amp; einfach</span></span>Futtergenerator</h2>
  <p>Hier haben Sie die Möglichkeit, das Futter ganz nach Ihren Anforderungen und den Bedürfnissen Ihrer Tiere individuell zusammenzustellen. Unser benutzerfreundlicher Generator ermöglicht es Ihnen, präzise Angaben zu den gewünschten Inhaltsstoffen bis hin zu speziellen Ernährungsbedürfnissen zu machen. Mit nur wenigen Klicks erhalten Sie eine maßgeschneiderte Empfehlung für Futter, das höchsten Qualitätsstandards entspricht.</p>
  <span class="btn">Zum Generator</span>
</div>

<h2 class="abs section-title partner-title"><span class="line1">Unsere<span class="script">Vertrauen &amp; Kompetenz</span></span>Partner &amp; Lieferanten</h2>
<div class="abs partners">
  <span>Kornfeld</span><span>Lactavo</span><span>Weidegrün Saaten</span><span>Nordhafen Futter</span>
</div>

<footer class="abs footer"></footer>
<div class="abs f-logo"><span class="dot"></span>Talgrund</div>
<div class="abs news">
  <h2 class="section-title"><span class="line1">Bleiben Sie<span class="script">E-Mail-Verteiler</span></span>auf dem Laufenden</h2>
  <input type="text" placeholder="Ihr Name">
  <input type="text" placeholder="Ihre E-Mail Adresse">
  <div class="check"><i></i>Ich akzeptiere die <a href="#">Datenschutzbestimmungen</a></div>
  <span class="btn">Absenden</span>
</div>
<div class="abs fcol" style="left:490px">
  <h5>Kontakt</h5>
  <p style="line-height:1.25">Talgrund Agrarhandel GbR<br>Feldstraße 4<br>91234 Musterau</p>
  <p style="margin-top:14px">+49 9876 543210</p>
  <p style="margin-top:16px">info@talgrund-agrar.de</p>
</div>
<ul class="abs fcol" style="left:683px">
  <h5>Info</h5>
  <li>AGB's</li><li>Datenschutz</li><li>Impressum</li><li>Cookie-Hinweis</li><li>Lieferbedingungen</li>
</ul>
<ul class="abs fcol" style="left:837px">
  <h5>Menü</h5>
  <li>Über uns</li><li>Produkte +</li><li>Partner</li><li>Downloads</li><li>Kontakt</li>
</ul>
<div class="abs fcol" style="left:974px">
  <h5>Zertifikate</h5>
  <div class="badge"><span class="mark"></span><span class="mark2"></span></div>
  <h5 style="margin-top:14px;margin-bottom:6px">Social Media</h5>
  <div class="social"><i></i><i></i><i></i></div>
</div>
<div class="abs bottom-bar">© 2023 Talgrund Agrarhandel GbR</div>

</body>
</html>
```